Harrowmere Freight, Project

Company Profile
Harrowmere Freight Sdn Bhd is a well established and experienced freight forwarder in Kuala Lumpur, Malaysia. We specialize in air and sea forwarding, Custom Brokerage and regulatory compliance services, inland transportation,
overseas freighting and warehousing and distribution management. With our dedicated qualified and experienced professionals, we are fully committed to serving our clients.

Our Mission
Based on the motto “Quick, Reliable and Polite”, Harrowmere Freight is dedicated to upholding the following three points corporate philosophy:
1. Adhering to the principle that “the customer always comes first”.
2. Contributing to the development of the local community.
3. Making it our duty to be responsible and sincere.

Our Edge
• One-Stop Logistics Solutions
• Extensive Network Throughout Malaysia
• Highly Qualified and Experienced Pool of Professionals
• Comprehensive IT Solutions
• Innovative and Customer-focused Solutions
• Flexible and Consistent in Managing Exceptions
• Total Supply Chain Visibility

Target Market(s)

We sell the logistics services to all the industry in Malaysia. (ONE Stop Logistics Solutions)

Industry/Entity Type

Logistic

Contact Information for Business Card

I want the back of the card to be white with the logo and slogan. i would like to see the logo on the front with the general info.

Requirements
Must have
• Name, Title, Office, Cell, Fax, Email, Address, Website
Nice to have
• Modern Design Business Card

```html
<!DOCTYPE html>
<html lang="en">
<head>
<meta charset="utf-8">
<title>Harrowmere Freight – Business Card</title>
<link href="https://fonts.googleapis.com/css2?family=Open+Sans:wght@400;600;700&display=swap" rel="stylesheet">
<style>
  :root {
    --blue: #2a9bd8;
    --blue-dark: #1f86c2;
    --ink: #3c3c3c;
    --grey: #6b6b6b;
    --card: #ffffff;
    --bg: #e9e6e1;
  }
  * { box-sizing: border-box; margin: 0; padding: 0; }
  html, body {
    width: 1200px; height: 950px; overflow: hidden;
    background: var(--bg);
    font-family: "Open Sans", Arial, sans-serif;
    color: var(--ink);
  }
  .canvas { position: relative; width: 1200px; height: 950px; }
  .card {
    position: absolute; left: 200px; width: 800px; height: 440px;
    background: var(--card); border-radius: 22px; overflow: hidden;
    box-shadow: 0 6px 18px rgba(0,0,0,.18);
  }
  .card--back { top: 30px; }
  .card--front { top: 490px; }

  /* back */
  .services { position: absolute; left: 56px; top: 58px; }
  .services__title { color: var(--blue); font-weight: 700; font-size: 26px; margin-bottom: 6px; }
  .services__list { list-style: none; font-size: 19px; line-height: 24.5px; color: var(--ink); }
  .services__slogan { margin-top: 8px; color: var(--blue); font-weight: 700; font-size: 19px; letter-spacing: .3px; }
  .brand { position: absolute; right: 60px; top: 110px; display: flex; align-items: center; gap: 14px; }
  .brand__dot { width: 22px; height: 22px; border-radius: 50%; background: var(--blue); }
  .brand__name { font-size: 34px; font-weight: 700; color: var(--ink); }

  /* front */
  .band { position: absolute; right: 0; top: 0; width: 210px; height: 100%; background: var(--blue); }
  .band__mark { position: absolute; right: 36px; top: 60px; display: flex; align-items: center; gap: 10px; }
  .band__dot { width: 16px; height: 16px; border-radius: 50%; background: #fff; }
  .band__name { font-size: 20px; font-weight: 700; color: #fff; }

  .contact { position: absolute; left: 56px; top: 50px; width: 500px; }
  .contact__name { color: var(--blue); font-size: 34px; font-weight: 700; line-height: 1.1; }
  .contact__title, .contact__email { font-size: 19px; color: var(--grey); line-height: 26px; }
  .divider { border: 0; border-top: 3px dotted var(--blue); margin: 12px 0; width: 440px; }
  .company { font-size: 18px; font-weight: 700; color: var(--ink); line-height: 25px; }
  .address { font-size: 18px; color: var(--ink); line-height: 25px; font-style: normal; }
  .lines { list-style: none; }
  .lines li { display: flex; align-items: center; gap: 12px; font-size: 19px; line-height: 29px; color: var(--ink); }
  .lines svg { width: 18px; height: 18px; fill: var(--blue); flex: none; }
</style>
</head>
<body>
<main class="canvas">

  <section class="card card--back" aria-label="Card back">
    <div class="services">
      <h2 class="services__title">We're Specialize In</h2>
      <ul class="services__list">
        <li>International Shipping (Air / Sea)</li>
        <li>Consolidation - NVOCC</li>
        <li>Project Management</li>
        <li>Supply Chain Management</li>
        <li>Tax Exemption Consultancy</li>
        <li>Custom Brokerage</li>
        <li>Transportation / Haulage</li>
        <li>Warehousing</li>
        <li>Packing</li>
        <li>Marine Insurance</li>
        <li>Distribution</li>
        <li>Door to Door</li>
      </ul>
      <p class="services__slogan">ONE STOP LOGISTICS SOLUTIONS</p>
    </div>
    <div class="brand">
      <span class="brand__dot"></span>
      <span class="brand__name">Harrowmere Freight</span>
    </div>
  </section>

  <section class="card card--front" aria-label="Card front">
    <div class="band">
      <div class="band__mark">
        <span class="band__dot"></span>
        <span class="band__name">Harrowmere</span>
      </div>
    </div>

    <div class="contact">
      <h1 class="contact__name">Azrulhakim</h1>
      <p class="contact__title">Managing Director</p>
      <p class="contact__email">azrul.hakim@harrowmere.com.my</p>
      <hr class="divider">
      <p class="company">HARROWMERE FREIGHT SDN. BHD. (1048236-K)</p>
      <address class="address">No. 14B, 2nd Floor, Jalan Seri Murni 3<br>Taman Murni Jaya, 41050 Klang<br>Selangor Darul Ehsan, Malaysia.</address>
      <hr class="divider">
      <ul class="lines">
        <li><svg viewBox="0 0 24 24" aria-label="Office"><path d="M6.6 10.8a15.1 15.1 0 0 0 6.6 6.6l2.2-2.2a1 1 0 0 1 1-.25 11.4 11.4 0 0 0 3.6.57 1 1 0 0 1 1 1V20a1 1 0 0 1-1 1A17 17 0 0 1 3 4a1 1 0 0 1 1-1h3.5a1 1 0 0 1 1 1c0 1.25.2 2.45.57 3.57a1 1 0 0 1-.25 1z"/></svg>(603) 5521 3087 / 3088</li>
        <li><svg viewBox="0 0 24 24" aria-label="Mobile"><path d="M7 1h10a2 2 0 0 1 2 2v18a2 2 0 0 1-2 2H7a2 2 0 0 1-2-2V3a2 2 0 0 1 2-2zm0 3v14h10V4zm5 15.5a1.2 1.2 0 1 0 0 2.4 1.2 1.2 0 0 0 0-2.4z"/></svg>+6012-448 2719</li>
        <li><svg viewBox="0 0 24 24" aria-label="Fax"><path d="M6 2h9l3 3v4H6zm-2 8h16a2 2 0 0 1 2 2v8H2v-8a2 2 0 0 1 2-2zm3 4v2h10v-2z"/></svg>(603) 5521 3090</li>
        <li><svg viewBox="0 0 24 24" aria-label="Website"><path d="M12 2a10 10 0 1 0 0 20 10 10 0 0 0 0-20zm6.9 6h-3a15.6 15.6 0 0 0-1.4-3.6A8 8 0 0 1 18.9 8zM12 4c.8 1.2 1.5 2.5 1.9 4h-3.8c.4-1.5 1.1-2.8 1.9-4zM4.3 14a8 8 0 0 1 0-4h3.4a16 16 0 0 0 0 4zm.8 2h3a15.6 15.6 0 0 0 1.4 3.6A8 8 0 0 1 5.1 16zm3-8h-3a8 8 0 0 1 4.4-3.6A15.6 15.6 0 0 0 8.1 8zM12 20c-.8-1.2-1.5-2.5-1.9-4h3.8c-.4 1.5-1.1 2.8-1.9 4zm2.3-6H9.7a14.7 14.7 0 0 1 0-4h4.6a14.7 14.7 0 0 1 0 4zm.2 5.6a15.6 15.6 0 0 0 1.4-3.6h3a8 8 0 0 1-4.4 3.6zm1.8-5.6a16 16 0 0 0 0-4h3.4a8 8 0 0 1 0 4z"/></svg>harrowmere.com.my</li>
      </ul>
    </div>
  </section>

</main>
</body>
</html>
```